VFX Company Business Card Design Project

The Kestrel Works is a decentralized Visual Effects Studio servicing the television and feature film industries.
Project Brief:
Take our logo that was previously designed on Pencil Harbor and make a double sided business card.
Requirements:
- Card MUST be double sided.
- Front of card MUST have the yellow part of our logo against the dark grey background.
- Back of card is completely up to the designer.
- Back of card must include the complete company logo.
Please follow these File Preparation guidelines:
http://printnook.ca/infopage?file=filetype_en&s=PrintNook_new&lang=en
Business

```html
<!DOCTYPE html>
<html lang="en">
<head>
<meta charset="utf-8">
<title>The Kestrel Works — Business Card</title>
<link href="https://fonts.googleapis.com/css2?family=Jost:wght@400;500;600&display=swap" rel="stylesheet">
<style>
  :root {
    --backdrop: #dcc3a8;
    --card: #262626;
    --slate: #5d6a6b;
    --swoosh: #e9ecdf;
    --yellow: #fbc52a;
    --ink-light: #f0f0ec;
    --brand-grey: #c7ccce;
    --label: #1e1e1e;
  }
  * { box-sizing: border-box; margin: 0; padding: 0; }
  html, body { width: 1200px; height: 788px; overflow: hidden; }
  body {
    position: relative;
    background: var(--backdrop);
    font-family: "Jost", sans-serif;
  }
  .side-label {
    position: absolute;
    font-size: 22px;
    color: var(--label);
    transform: translateX(-50%);
    white-space: nowrap;
  }
  .card {
    position: absolute;
    width: 525px;
    height: 300px;
    border-radius: 22px;
    background: var(--card);
    overflow: hidden;
    box-shadow: 0 4px 10px rgba(0,0,0,0.35);
  }
  .card--back { left: 338px; top: 78px; }
  .card--front-one { left: 54px; top: 445px; }
  .card--front-two { left: 622px; top: 445px; }

  .wave { position: absolute; inset: 0; }

  .brand {
    position: absolute;
    display: flex;
    align-items: center;
    gap: 12px;
    font-weight: 500;
    white-space: nowrap;
  }
  .brand__dot { border-radius: 50%; flex: none; }

  .card--back .brand { left: 42px; top: 30px; font-size: 32px; color: var(--brand-grey); }

  .contact-person { position: absolute; left: 42px; top: 135px; color: var(--ink-light); }
  .contact-person__name { font-size: 20px; line-height: 1; }
  .contact-person__role { font-size: 13px; letter-spacing: 0.5px; margin-top: 6px; color: #cfcfcf; }
  .contact-person__phones { margin-top: 14px; font-size: 14px; line-height: 25px; }
  .contact-person__phones b, .contact-office b { font-style: italic; font-weight: 600; }

  .contact-office {
    position: absolute;
    right: 27px;
    top: 205px;
    text-align: right;
    color: var(--ink-light);
    font-size: 14px;
    line-height: 21px;
  }
  .contact-office .address { font-size: 12.5px; line-height: 18px; }

  .card--front-one .brand {
    left: 50%; top: 108px; transform: translateX(-50%);
    font-size: 44px; font-weight: 600; color: var(--yellow);
  }
  .card--front-one .brand__dot { width: 54px; height: 54px; background: var(--yellow); }

  .card--front-two .brand {
    left: 50%; top: 124px; transform: translateX(-50%);
    font-size: 36px; color: var(--brand-grey);
  }
  .card--front-two .brand__dot { width: 44px; height: 44px; background: var(--yellow); }

  .site {
    position: absolute;
    left: 0; right: 0; bottom: 18px;
    text-align: center;
    font-size: 20px;
    letter-spacing: 3.5px;
    color: var(--ink-light);
  }
</style>
</head>
<body>
  <div class="side-label" style="left:600px; top:32px;">Back</div>
  <div class="side-label" style="left:327px; top:403px;">Front - 1</div>
  <div class="side-label" style="left:900px; top:403px;">Front - 2</div>

  <section class="card card--back">
    <svg class="wave" viewBox="0 0 525 300" width="525" height="300" aria-hidden="true">
      <path d="M0,268 C110,292 215,270 320,205 C400,150 455,115 525,110 L525,300 L0,300 Z" fill="var(--slate)"/>
      <path d="M0,255 C110,282 215,262 315,198 C395,145 452,110 525,100 L525,110 C455,117 400,152 322,207 C218,275 110,295 0,272 Z" fill="#111"/>
      <path d="M0,238 C100,268 205,252 305,190 C390,138 450,107 525,98 L525,102 C455,113 398,148 312,203 C210,268 100,280 0,262 Z" fill="var(--swoosh)"/>
    </svg>
    <div class="brand">The Kestrel Works</div>
    <div class="contact-person">
      <div class="contact-person__name">Your Name</div>
      <div class="contact-person__role">Designation</div>
      <div class="contact-person__phones">
        <div><b>p :</b> 123-456-7890</div>
        <div><b>c :</b> 123-456-7890</div>
      </div>
    </div>
    <div class="contact-office">
      <div><b>w</b> : www.website.com</div>
      <div><b>e</b> : info@website.com</div>
      <div class="address">0000#, Area Name<br>State Name, Country code</div>
    </div>
  </section>

  <section class="card card--front-one">
    <div class="brand"><span class="brand__dot"></span>The Kestrel Works</div>
    <div class="site">www.website.com</div>
  </section>

  <section class="card card--front-two">
    <div class="brand"><span class="brand__dot"></span>The Kestrel Works</div>
    <div class="site">www.website.com</div>
  </section>
</body>
</html>
```